Business Card Design For A Renovation Contractor Company

We need a business card for a new company based in Singapore, our company name is "RB Tolvane". We are a renovation contractor that builds designs into reality. We build more of F&B restaurants, retail stores and commercial offices. We work very closely with designers. The final design should communicate to our client that we are a company that you can trust, that will plan and complete your project without giving you a headache. I like my client to remember my company as "RB". The beauty of SIMPLE is important.

Industry/Entity Type

Contractor

Requirements
Nice to have
• Black or Red base

```html
<!DOCTYPE html>
<html lang="en">
<head>
<meta charset="utf-8">
<title>RB Tolvane – Business Card</title>
<link rel="stylesheet" href="https://fonts.googleapis.com/css2?family=Jost:wght@400;500;700&display=swap">
<style>
  :root {
    --bg: #e9e9ee;
    --card: #ffffff;
    --ink: #1c1c1c;
    --grey: #555558;
    --rule: #9a9a9e;
    --red: #e0222b;
  }
  * { box-sizing: border-box; margin: 0; padding: 0; }
  html, body {
    width: 1200px; height: 987px; overflow: hidden;
    background: var(--bg);
    font-family: "Jost", "Futura", sans-serif;
    color: var(--ink);
  }
  .canvas { position: relative; width: 1200px; height: 987px; }
  .card {
    position: absolute;
    width: 620px; height: 354px;
    background: var(--card);
    border-radius: 26px;
    box-shadow: 0 6px 18px rgba(0,0,0,0.12);
  }
  /* back */
  .card-back { left: 520px; top: 70px; }
  .card-back .brand {
    position: absolute; left: 120px; top: 96px; width: 380px;
  }
  .wordmark {
    display: flex; align-items: center; gap: 14px;
    font-weight: 400; color: var(--ink); line-height: 1;
    letter-spacing: -1px; white-space: nowrap;
  }
  .wordmark .dot {
    flex: none; border-radius: 50%; background: var(--red);
  }
  .card-back .wordmark { font-size: 60px; }
  .card-back .wordmark .dot { width: 40px; height: 40px; }
  .tagline {
    border-top: 1.5px solid var(--ink);
    margin-top: 8px; padding-top: 2px;
    color: var(--ink); letter-spacing: 0.5px; white-space: nowrap;
  }
  .card-back .tagline { font-size: 24px; }
  .card-back .website {
    position: absolute; left: 120px; top: 248px;
    font-size: 20px; letter-spacing: 5px; color: var(--grey);
  }
  .website .accent { color: var(--red); }
  /* front */
  .card-front { left: 60px; top: 470px; }
  .card-front .brand { position: absolute; left: 40px; top: 112px; width: 250px; }
  .card-front .wordmark { font-size: 40px; gap: 10px; }
  .card-front .wordmark .dot { width: 30px; height: 30px; }
  .card-front .tagline { font-size: 16px; margin-top: 6px; }
  .divider {
    position: absolute; left: 320px; top: 40px;
    width: 2px; height: 240px; background: var(--rule);
  }
  .divider::before {
    content: ""; position: absolute; left: 0; top: 0;
    width: 4px; height: 40px; background: var(--red);
  }
  .contact { position: absolute; left: 344px; top: 38px; }
  .contact .name { font-size: 28px; font-weight: 700; color: var(--red); line-height: 1.1; }
  .contact .title { font-size: 18px; color: var(--grey); margin-bottom: 14px; }
  .contact .lines { list-style: none; font-size: 18px; color: var(--ink); line-height: 1.35; }
  .contact .lines span { display: inline-block; width: 26px; }
  .contact .address { margin-top: 10px; font-size: 18px; color: var(--grey); line-height: 1.3; }
</style>
</head>
<body>
<main class="canvas">
  <section class="card card-back" aria-label="Card back">
    <div class="brand">
      <div class="wordmark"><span class="dot"></span>RB Tolvane</div>
      <div class="tagline">plans made solid, built right</div>
    </div>
    <div class="website">www.<span class="accent">rbtolvane</span>.com</div>
  </section>

  <section class="card card-front" aria-label="Card front">
    <div class="brand">
      <div class="wordmark"><span class="dot"></span>RB Tolvane</div>
      <div class="tagline">plans made solid, built right</div>
    </div>
    <div class="divider"></div>
    <div class="contact">
      <div class="name">Your Name</div>
      <div class="title">Title</div>
      <ul class="lines">
        <li><span>P:</span>123-456-7890</li>
        <li><span>C:</span>456-210-7735</li>
        <li><span>E:</span>info@rbtolvane.com</li>
        <li><span>W:</span>www.rbtolvane.com</li>
      </ul>
      <div class="address">Door No. Street Name<br>City Name, State, Zip Code</div>
    </div>
  </section>
</main>
</body>
</html>
```